Rosko Tamblin

I am a songwriter and would like to include a bio, pictures, discography, CD covers and access to some of my music

Target Market(s)

Music Lovers, songwriters publishers

Coding

Coded - Design and coding required

Number of Pages Required

5+ page

Requirements
Must have
• Pictures of my CD covers, pictures of me and either my Music or links to my music
Nice to have
Should not have
• cartoons

```html
<!DOCTYPE html>
<html lang="en">
<head>
<meta charset="utf-8">
<title>Rosko Tamblin — Songwriter</title>
<link href="https://fonts.googleapis.com/css2?family=Montserrat:wght@300;400;600;700;800&family=Titillium+Web:wght@300;400&family=Arimo:wght@400;700&display=swap" rel="stylesheet">
<style>
:root{
  --yellow:#fbb53b;
  --orange:#f7a531;
  --cream:#fdebc4;
  --grey:#efefef;
  --ink:#222222;
  --text:#555555;
  --muted:#8a8a8a;
  --dark:#2b2b2b;
  --white:#ffffff;
}
*{margin:0;padding:0;box-sizing:border-box}
html,body{width:1200px;height:4152px;overflow:hidden;background:var(--white)}
body{font-family:"Arimo",Arial,sans-serif;color:var(--text)}
.page{position:relative;width:1200px;height:4152px;overflow:hidden}
.abs{position:absolute}

/* header */
.site-header{left:0;top:0;width:1200px;height:86px;background:var(--white)}
.brand{left:113px;top:20px;font-family:"Titillium Web",sans-serif;font-size:38px;font-weight:400;color:var(--ink);line-height:1}
.nav{left:435px;top:36px;display:flex;gap:25px;font-family:"Montserrat",sans-serif;font-size:16px;color:var(--ink)}
.nav .active{color:var(--orange)}
.btn{display:inline-block;background:var(--orange);color:var(--white);font-family:"Montserrat",sans-serif;font-weight:700;border-radius:24px;text-align:center}
.nav-btn{left:939px;top:24px;width:143px;height:46px;line-height:46px;font-size:15px}

/* hero */
.hero{left:0;top:86px;width:1200px;height:634px;background:
  radial-gradient(ellipse 260px 420px at 720px 330px,#d9d3c8 0%,#6b5a4a 55%,transparent 80%),
  linear-gradient(170deg,#3a120a 0%,#a3300e 18%,#f06a14 32%,#ffb040 40%,#c4400e 52%,#5a180a 70%,#1e0806 100%)}
.hero-title{left:169px;top:530px;font-family:"Montserrat",sans-serif;font-weight:800;font-size:55px;line-height:62px;color:var(--white);letter-spacing:1px}
.hero-dashes{left:503px;top:616px;display:flex;gap:10px}
.hero-dashes span{width:32px;height:4px;background:var(--white)}
.hero-edge{left:0;top:650px}

/* about */
.about-ring{left:132px;top:737px;width:268px;height:268px;border-radius:50%;background:var(--cream)}
.about-photo{left:198px;top:787px;width:378px;height:378px;border-radius:50%;background:radial-gradient(circle at 50% 45%,#e9ded2 0%,#b48a62 40%,#7a5a3c 75%,#5a4430 100%)}
.section-title{font-family:"Montserrat",sans-serif;font-weight:400;color:var(--ink);letter-spacing:8px;line-height:1}
.about-title{left:614px;top:772px;font-size:54px}
.about-text{left:616px;top:840px;width:411px;font-size:13.2px;line-height:19.5px;text-align:justify;color:var(--text)}
.about-btn{left:616px;top:1113px;width:137px;height:39px;line-height:39px;font-size:14px}

/* cd covers */
.band-yellow{left:0;width:1200px;background:var(--yellow)}
.band-grey{left:0;width:1200px;background:var(--grey)}
.center-title{left:0;width:1200px;text-align:center;font-size:55px}
.cd-card{top:1419px;width:200px;height:275px;background:var(--white);text-align:center}
.cd-art{width:142px;height:142px;border-radius:50%;margin:20px auto 0}
.cd-name{margin-top:18px;font-family:"Montserrat",sans-serif;font-weight:600;font-size:15.5px;color:var(--ink)}
.cd-desc{margin:10px auto 0;width:150px;font-size:13px;line-height:19px;color:var(--text)}
.arrow{top:1517px}

/* discography */
.subtitle{left:0;width:1200px;text-align:center;font-size:13.4px;line-height:19.5px;color:var(--text)}
.disc-art{top:2005px;width:231px;height:289px}
.disc-card{top:2189px;width:204px;height:134px;background:var(--white);padding:26px 10px 0 21px}
.disc-author{font-family:"Montserrat",sans-serif;font-size:13.5px;letter-spacing:1.5px;color:var(--muted)}
.disc-title{margin-top:14px;font-family:"Montserrat",sans-serif;font-size:20px;line-height:25px;letter-spacing:.5px;color:var(--ink);white-space:nowrap}

/* music */
.track{width:374px;height:47px;background:var(--white);display:flex;align-items:center;padding:0 12px;font-size:13.5px;color:var(--ink)}
.track-name{flex:1}
.track-time{color:var(--muted);font-size:12.5px;margin-right:18px}

/* footer */
.site-footer{left:0;top:3771px;width:1200px;height:381px;background:var(--dark)}
.foot-brand{left:169px;top:3842px;font-family:"Titillium Web",sans-serif;font-weight:300;font-size:38px;line-height:37px;color:#b9b9b9}
.social{top:3936px;width:28px;height:28px;border-radius:50%;border:2px solid #cfcfcf}
.foot-head{top:3846px;font-family:"Montserrat",sans-serif;font-weight:700;font-size:14px;color:var(--white);letter-spacing:.5px}
.foot-text{font-size:12.5px;line-height:19.5px;color:#d2d2d2}
.email-field{left:686px;top:3963px;width:165px;border-bottom:1px solid #6a6a6a;padding-bottom:8px;font-size:11px;font-style:italic;color:#bdbdbd}
.signup{left:686px;top:4005px;width:100px;height:36px;line-height:36px;font-size:12px;font-weight:400}
.links{left:916px;top:3882px;list-style:none}
.foot-rule{left:150px;top:4076px;width:898px;height:1px;background:#4a4a4a}
.copyright{left:0;top:4106px;width:1200px;text-align:center;font-size:13px;color:#d2d2d2}
</style>
</head>
<body>
<div class="page">

  <header class="abs site-header">
    <div class="abs brand">Rosko Tamblin</div>
    <nav class="abs nav">
      <span class="active">HOME</span><span>BIO</span><span>PICTURES</span><span>DISCOGRAPHY</span><span>CD COVERS</span>
    </nav>
    <span class="abs btn nav-btn">MY MUSIC</span>
  </header>

  <section class="abs hero" role="img" aria-label="Photo of the songwriter standing at night in front of a glowing orange lava crater"></section>
  <h1 class="abs hero-title">ROSKO<br>TAMBLIN.</h1>
  <div class="abs hero-dashes"><span></span><span></span><span></span><span></span></div>
  <svg class="abs hero-edge" width="1200" height="72" viewBox="0 0 1200 72">
    <polygon points="0,56 1200,16 1200,68 0,62" fill="#fbb53b"/>
    <polygon points="0,62 1200,68 1200,72 0,72" fill="#ffffff"/>
  </svg>

  <section>
    <div class="abs about-ring"></div>
    <div class="abs about-photo" role="img" aria-label="Portrait of the songwriter smiling in a white shirt in front of an adobe wall"></div>
    <h2 class="abs section-title about-title">ABOUT ME</h2>
    <p class="abs about-text">Rosko Tamblin was born and raised in Houston, Texas. He began playing music at the age of eight when his sister returned home from summer camp and asked her parents to buy her a baritone ukulele. She taught her younger brother some chords on the ukulele and he was hooked. The following spring, they went to one of the border towns in Mexico and bought a Mexican guitar for $12. They restrung it with nylon strings and Tamblin began to learn how to play the guitar. He took guitar lessons at a local music store and learned how to play the hits of the day by groups like Dormer's Drifters, the Quillmen, and the Pale Harbors. He got his first electric guitar when he was about 10 years old. He began jamming with other musicians when he was 13 or 14. They were much more experienced than he and introduced him to the blues.</p>
    <span class="abs btn about-btn">READ MORE</span>
  </section>

  <section class="abs band-yellow" style="top:1247px;height:531px"></section>
  <h2 class="abs section-title center-title" style="top:1328px">CD COVERS</h2>
  <svg class="abs arrow" style="left:98px" width="36" height="80" viewBox="0 0 36 80"><polyline points="34,2 2,40 34,78" fill="none" stroke="#ffffff" stroke-width="2"/></svg>
  <svg class="abs arrow" style="left:1066px" width="36" height="80" viewBox="0 0 36 80"><polyline points="2,2 34,40 2,78" fill="none" stroke="#ffffff" stroke-width="2"/></svg>
  <article class="abs cd-card" style="left:173px">
    <div class="cd-art" role="img" aria-label="CD cover: man with guitar on a swirling purple background" style="background:radial-gradient(circle,#e7a24a 0%,#b52b6a 55%,#5a1a6a 100%)"></div>
    <div class="cd-name">CD Cover Name</div>
    <p class="cd-desc">Sed ut perspiciatis unde omnis iste natusrsi</p>
  </article>
  <article class="abs cd-card" style="left:390px">
    <div class="cd-art" role="img" aria-label="CD cover: burning record beside a coffee cup" style="background:radial-gradient(circle at 40% 45%,#f5a030 0%,#a9401c 45%,#3b3028 100%)"></div>
    <div class="cd-name">CD Cover Name</div>
    <p class="cd-desc">Sed ut perspiciatis unde omnis iste natusrsi</p>
  </article>
  <article class="abs cd-card" style="left:610px">
    <div class="cd-art" role="img" aria-label="CD cover: silhouette against a stormy lightning sky" style="background:radial-gradient(circle at 40% 35%,#9a8fb0 0%,#7a2a2a 50%,#111111 100%)"></div>
    <div class="cd-name">CD Cover Name</div>
    <p class="cd-desc">Sed ut perspiciatis unde omnis iste natusrsi</p>
  </article>
  <article class="abs cd-card" style="left:827px">
    <div class="cd-art" role="img" aria-label="CD cover: ship on rough sea with title text" style="background:radial-gradient(circle,#d8894a 0%,#2f4a78 55%,#1a2a4a 100%)"></div>
    <div class="cd-name">CD Cover Name</div>
    <p class="cd-desc">Sed ut perspiciatis unde omnis iste natusrsi</p>
  </article>

  <section class="abs band-grey" style="top:1778px;height:637px"></section>
  <h2 class="abs section-title center-title" style="top:1850px">DISCOGRAPHY</h2>
  <p class="abs subtitle" style="top:1918px">Sed ut perspiciatis unde omnis iste natus error sit voluptatem accus antium doloremque laudantium,<br>totam rem aperiam, eaque ipsa quae ab illo inventore veritatis et quasi architecto beatae vitae</p>
  <div class="abs disc-art" style="left:173px;background:linear-gradient(160deg,#1a1a1a 0%,#5a5a5a 45%,#e8e8e8 60%,#1a1a1a 100%)" role="img" aria-label="Album art: black and white sketch of a guitarist in a hat"></div>
  <div class="abs disc-card" style="left:221px"><div class="disc-author">DAVISD</div><div class="disc-title">SED UTPESPIC<br>IATISUNDE</div></div>
  <div class="abs disc-art" style="left:473px;background:linear-gradient(160deg,#c7d8e6 0%,#e9d9c7 45%,#f1c8c8 70%,#d8c8dc 100%)" role="img" aria-label="Album art: pastel collage with title banners and a child's photo"></div>
  <div class="abs disc-card" style="left:521px"><div class="disc-author">JHONSMITH</div><div class="disc-title">SED UTPESPIC<br>IATISUNDE</div></div>
  <div class="abs disc-art" style="left:774px;background:linear-gradient(180deg,#2d4a7a 0%,#5a7090 40%,#d8dce0 65%,#2a3e5a 100%)" role="img" aria-label="Album art: ship battling waves on a stormy sea"></div>
  <div class="abs disc-card" style="left:823px"><div class="disc-author">MARIDLOR</div><div class="disc-title">SED UTPESPIC<br>IATISUNDE</div></div>

  <section class="abs band-yellow" style="top:2415px;height:550px"></section>
  <h2 class="abs section-title center-title" style="top:2487px">MY MUSIC</h2>
  <p class="abs subtitle" style="top:2556px">Sed ut perspiciatis unde omnis iste natus error sit voluptatem accus antium doloremque laudantium,<br>totam rem aperiam, eaque ipsa quae ab illo inventore veritatis et quasi architecto beatae vitae dicta<br>sunt explicabo. Nemo enim ipsam voluptatem quia voluptas sit aspernatur aut odit aut fugit</p>

  <div class="abs track" style="left:218px;top:2644px"><span class="track-name">Sed utpespic iatisunde</span><span class="track-time">4:35 min</span><svg width="20" height="20" viewBox="0 0 20 20"><path d="M6 4 L18 1 V14" fill="none" stroke="#333" stroke-width="2"/><circle cx="4.5" cy="16" r="2.8" fill="#333"/><circle cx="15.5" cy="14" r="2.8" fill="#333"/><path d="M6 4 V16" stroke="#333" stroke-width="2"/></svg></div>
  <div class="abs track" style="left:608px;top:2644px"><span class="track-name">Sed utpespic iatisunde</span><span class="track-time">4:35 min</span><svg width="20" height="20" viewBox="0 0 20 20"><path d="M6 4 L18 1 V14" fill="none" stroke="#333" stroke-width="2"/><circle cx="4.5" cy="16" r="2.8" fill="#333"/><circle cx="15.5" cy="14" r="2.8" fill="#333"/><path d="M6 4 V16" stroke="#333" stroke-width="2"/></svg></div>
  <div class="abs track" style="left:218px;top:2701px"><span class="track-name">Sed utpespic iatisunde</span><span class="track-time">4:35 min</span><svg width="20" height="20" viewBox="0 0 20 20"><path d="M6 4 L18 1 V14" fill="none" stroke="#333" stroke-width="2"/><circle cx="4.5" cy="16" r="2.8" fill="#333"/><circle cx="15.5" cy="14" r="2.8" fill="#333"/><path d="M6 4 V16" stroke="#333" stroke-width="2"/></svg></div>
  <div class="abs track" style="left:608px;top:2701px"><span class="track-name">Sed utpespic iatisunde</span><span class="track-time">4:35 min</span><svg width="20" height="20" viewBox="0 0 20 20"><path d="M6 4 L18 1 V14" fill="none" stroke="#333" stroke-width="2"/><circle cx="4.5" cy="16" r="2.8" fill="#333"/><circle cx="15.5" cy="14" r="2.8" fill="#333"/><path d="M6 4 V16" stroke="#333" stroke-width="2"/></svg></div>
  <div class="abs track" style="left:218px;top:2759px"><span class="track-name">Sed utpespic iatisunde</span><span class="track-time">4:35 min</span><svg width="20" height="20" viewBox="0 0 20 20"><path d="M6 4 L18 1 V14" fill="none" stroke="#333" stroke-width="2"/><circle cx="4.5" cy="16" r="2.8" fill="#333"/><circle cx="15.5" cy="14" r="2.8" fill="#333"/><path d="M6 4 V16" stroke="#333" stroke-width="2"/></svg></div>
  <div class="abs track" style="left:608px;top:2759px"><span class="track-name">Sed utpespic iatisunde</span><span class="track-time">4:35 min</span><svg width="20" height="20" viewBox="0 0 20 20"><path d="M6 4 L18 1 V14" fill="none" stroke="#333" stroke-width="2"/><circle cx="4.5" cy="16" r="2.8" fill="#333"/><circle cx="15.5" cy="14" r="2.8" fill="#333"/><path d="M6 4 V16" stroke="#333" stroke-width="2"/></svg></div>
  <div class="abs track" style="left:218px;top:2818px"><span class="track-name">Sed utpespic iatisunde</span><span class="track-time">4:35 min</span><svg width="20" height="20" viewBox="0 0 20 20"><path d="M6 4 L18 1 V14" fill="none" stroke="#333" stroke-width="2"/><circle cx="4.5" cy="16" r="2.8" fill="#333"/><circle cx="15.5" cy="14" r="2.8" fill="#333"/><path d="M6 4 V16" stroke="#333" stroke-width="2"/></svg></div>
  <div class="abs track" style="left:608px;top:2818px"><span class="track-name">Sed utpespic iatisunde</span><span class="track-time">4:35 min</span><svg width="20" height="20" viewBox="0 0 20 20"><path d="M6 4 L18 1 V14" fill="none" stroke="#333" stroke-width="2"/><circle cx="4.5" cy="16" r="2.8" fill="#333"/><circle cx="15.5" cy="14" r="2.8" fill="#333"/><path d="M6 4 V16" stroke="#333" stroke-width="2"/></svg></div>

  <section class="abs band-grey" style="top:2965px;height:806px"></section>
  <h2 class="abs section-title center-title" style="top:3034px">GALLERY</h2>
  <p class="abs subtitle" style="top:3101px">Sed ut perspiciatis unde omnis iste natus error sit voluptatem accus antium doloremque laudantium,<br>totam rem aperiam, eaque ipsa quae ab illo inventore veritatis et quasi architecto beatae vitae</p>
  <div class="abs tile" style="left:173px;top:3170px;width:219px;height:240px;background:linear-gradient(160deg,#1a1a1a 0%,#6a6a6a 45%,#e6e6e6 62%,#1a1a1a 100%)" role="img" aria-label="Album art: sketch of a guitarist in a hat"></div>
  <div class="abs tile" style="left:411px;top:3170px;width:220px;height:240px;background:linear-gradient(180deg,#8f86a8 0%,#4a3048 45%,#7a2020 75%,#1a1010 100%)" role="img" aria-label="Album art: silhouette under a lightning storm"></div>
  <div class="abs tile" style="left:650px;top:3170px;width:377px;height:240px;background:radial-gradient(ellipse 90px 140px at 190px 120px,#e4ddd2 0%,#6a5040 60%,transparent 80%),linear-gradient(180deg,#2a0c06 0%,#c84a10 40%,#ffa838 55%,#8a2a0a 75%,#1a0806 100%)" role="img" aria-label="Photo of the songwriter at the lava crater at night"></div>
  <div class="abs tile" style="left:173px;top:3428px;width:375px;height:242px;background:radial-gradient(ellipse at 35% 55%,#ffd23a 0%,#f07a18 35%,#a32a10 65%,#6a4a3a 100%)" role="img" aria-label="Album art: flames over a record beside a coffee cup and sugar jar"></div>
  <div class="abs tile" style="left:566px;top:3428px;width:221px;height:242px;background:radial-gradient(ellipse at 50% 40%,#e8dfd2 0%,#a7835e 50%,#6e5238 100%)" role="img" aria-label="Photo of the songwriter in a white shirt by an adobe wall"></div>
  <div class="abs tile" style="left:807px;top:3428px;width:220px;height:242px;background:linear-gradient(180deg,#2d4a7a 0%,#60768f 40%,#d6dadf 62%,#263a55 85%,#c78838 100%)" role="img" aria-label="Album art: ship on a stormy sea"></div>

  <footer class="abs site-footer"></footer>
  <div class="abs foot-brand">Rosko<br>Tamblin</div>
  <span class="abs social" style="left:173px"></span>
  <span class="abs social" style="left:209px"></span>
  <span class="abs social" style="left:245px"></span>
  <span class="abs social" style="left:281px"></span>

  <h3 class="abs foot-head" style="left:403px">PODACAST</h3>
  <p class="abs foot-text" style="left:403px;top:3882px;width:213px">Morbi pharetra blandit faucibure eros turpis, scelerisque in nisl anatis blandit sem. Cras quis dui vitae puus interdum sollicitudin ut ut odiolerisqu ein nisl anatis blandit sernas quis dui vitae puus interdum sollictut od.</p>

  <h3 class="abs foot-head" style="left:686px">NEWSLETTER</h3>
  <p class="abs foot-text" style="left:686px;top:3882px;width:180px">Subscribe to us to get and receive the latest news, sales and updates.</p>
  <div class="abs email-field">Email Address:</div>
  <span class="abs btn signup">SIGN UP</span>

  <h3 class="abs foot-head" style="left:916px">LINKS</h3>
  <ul class="abs foot-text links">
    <li>Sed ut perspiciatis</li>
    <li>Unde omnis iste natus</li>
    <li>Voluptatem accusan</li>
    <li>Tium doloremque</li>
    <li>Haudantium</li>
    <li>Tum doloremque</li>
  </ul>

  <div class="abs foot-rule"></div>
  <p class="abs copyright">© 2020 All rights are reserved. Privacy | Terms of use</p>

</div>
</body>
</html>
```